Flat Belly Design Graphics for Social

I want to create 9 social media graphics (new Instagram size 4:5 (1080 x 1350 pixels) focusing on our Flat Belly Graphics, using the pics attached. Use the attached pics, NO RANDOM STOCK PHOTOGRAPHY. For the color scheme of the graphics, the color palette is attached. YOU MUST POST ALL 9 GRAPHICS IN ONE ENTRY.
Using the 3 titles below, create one set of graphics. 1) with all text, then for the others, use the pictures as detailed below in IMPORTANT:
1. Ten-Week Bright Morning Reboot
2. The Quick Garden Kitchen Menu Guide
3. Studio Habits for Lasting Energy Past Midlife - Zero Gym Needed
IMPORTANT:
Only use RK Pic 1 and RK Pic 2 with the title, Ten-Week Bright Morning Reboot
Only use meal plan1 and meal plan2 pics with the title, Quick Garden Kitchen Menu Guide
Only use studio habits 1 and studio habits 2 pics with the title, Studio Habits for Lasting Energy Past Midlife - Zero Gym Needed
women over 40

```html
<!DOCTYPE html>
<html lang="en">
<head>
<meta charset="utf-8">
<title>Morning Reboot Social Set</title>
<link href="https://fonts.googleapis.com/css2?family=Oswald:wght@400;500;600;700&display=swap" rel="stylesheet">
<style>
  :root{
    --backdrop:#230d14;
    --blush:#f9eded;
    --pine:#344e4a;
    --rose:#e296ae;
    --rose-text:#db7093;
    --teal-text:#63b3a3;
    --ring-outer:#fbe1e8;
    --ring-mid:#f7cfdc;
    --ring-grey:#d9cfd1;
    --white:#ffffff;
  }
  *{margin:0;padding:0;box-sizing:border-box}
  html,body{width:1074px;height:1200px;overflow:hidden;background:var(--backdrop)}
  body{font-family:'Oswald',sans-serif;position:relative}
  .card{position:absolute;width:259px;height:323px;background:var(--blush);overflow:hidden}
  .col-1{left:126px}.col-2{left:408px}.col-3{left:689px}
  .row-1{top:94px}.row-2{top:438px}.row-3{top:782px}
  .abs{position:absolute}
  .line{display:block;line-height:1;white-space:nowrap}

  /* text-only row */
  .tag{position:absolute;left:0;top:61px;height:40px;padding:0 16px 0 22px;border-radius:0 20px 20px 0;display:flex;align-items:center;font-weight:600;font-size:30px}
  .tag--pine{background:var(--pine);color:var(--rose-text)}
  .tag--rose{background:var(--rose);color:var(--pine)}
  .headline{position:absolute;left:22px;font-weight:600;color:var(--pine)}
  .band{position:absolute;left:0;width:100%;display:flex;flex-direction:column;justify-content:center;padding-left:22px;color:var(--white);font-weight:600}
  .band--rose{background:var(--rose)}
  .band--pine{background:var(--pine)}

  /* photo placeholders */
  .photo{position:absolute}
  .photo--round{border-radius:50%}

  /* caption panels */
  .panel{position:absolute;left:11px;top:205px;width:237px;height:107px;display:flex;flex-direction:column;align-items:center;justify-content:center;text-align:center;gap:3px}
  .panel--pine{background:var(--pine)}
  .panel--rose{background:var(--rose)}
  .kicker{font-weight:500;font-size:20px}
  .title{font-weight:700;font-size:28px}
  .spaced{font-weight:500;font-size:18px;letter-spacing:5px;color:var(--white)}
  .spaced--small{font-size:11px;letter-spacing:1.2px}
  .c-white{color:var(--white)}.c-rose{color:var(--rose-text)}.c-teal{color:var(--teal-text)}.c-pine{color:var(--pine)}
</style>
</head>
<body>

<!-- Row 1: text only -->
<section class="card col-1 row-1">
  <div class="tag tag--pine">Ten-Week</div>
  <span class="headline line" style="top:110px;font-size:34px">Bright Morning</span>
  <div class="band band--rose" style="top:158px;height:56px"><span class="line" style="font-size:40px">Reboot</span></div>
</section>

<section class="card col-2 row-1">
  <div class="tag tag--rose">Quick</div>
  <span class="headline line" style="top:110px;font-size:34px">Garden Kitchen</span>
  <div class="band band--pine" style="top:158px;height:56px"><span class="line" style="font-size:40px">Menu Guide</span></div>
</section>

<section class="card col-3 row-1">
  <div class="tag tag--pine">Studio</div>
  <span class="headline line" style="top:106px;font-size:36px">Habits for</span>
  <span class="headline line" style="top:153px;font-size:31px;color:var(--rose-text);font-weight:700">LASTING ENERGY</span>
  <div class="band band--rose" style="top:200px;height:123px;padding-left:20px;gap:6px;justify-content:flex-start;padding-top:12px">
    <span class="line" style="font-size:38px">Past Midlife -</span>
    <span class="line" style="font-size:24px;font-weight:500">Zero Gym Needed</span>
  </div>
</section>

<!-- Row 2: circle photos -->
<section class="card col-1 row-2">
  <div class="photo photo--round" style="left:18px;top:31px;width:224px;height:224px;background:var(--ring-outer)"></div>
  <div class="photo photo--round" style="left:41px;top:54px;width:178px;height:178px;background:var(--ring-mid)"></div>
  <div class="photo" role="img" aria-label="Smiling woman in a white cropped sweater pointing to her waist" style="left:50px;top:20px;width:160px;height:186px;border-radius:80px 80px 0 0;background:linear-gradient(180deg,#e9dcd8 0%,#f4efee 60%,#3a3336 100%)"></div>
  <div class="panel panel--pine">
    <span class="line kicker c-teal">Ten-Week</span>
    <span class="line title"><span class="c-white">BRIGHT</span> <span class="c-rose">MORNING</span></span>
    <span class="line spaced">Reboot</span>
  </div>
</section>

<section class="card col-2 row-2">
  <div class="photo photo--round" style="left:17px;top:25px;width:224px;height:224px;background:var(--ring-grey)"></div>
  <div class="photo photo--round" style="left:27px;top:35px;width:204px;height:204px;background:var(--pine)"></div>
  <div class="photo photo--round" role="img" aria-label="Overhead table of chicken, berries, asparagus and a meal plan sheet" style="left:38px;top:46px;width:182px;height:182px;background:radial-gradient(circle at 50% 55%,#f3f1ee 0%,#8a5a3c 45%,#4b2c1f 100%)"></div>
  <div class="panel panel--rose">
    <span class="line kicker c-pine">Quick</span>
    <span class="line title c-pine">GARDEN KITCHEN</span>
    <span class="line spaced">Menu Guide</span>
  </div>
</section>

<section class="card col-3 row-2">
  <div class="photo photo--round" style="left:18px;top:27px;width:224px;height:224px;background:var(--ring-outer)"></div>
  <div class="photo photo--round" style="left:31px;top:40px;width:198px;height:198px;background:var(--ring-mid)"></div>
  <div class="photo photo--round" role="img" aria-label="Two women sharing a whispered secret, one looking surprised" style="left:41px;top:50px;width:178px;height:178px;background:linear-gradient(135deg,#c7b8aa 0%,#8d6a55 50%,#e7e1dd 100%)"></div>
  <div class="panel panel--pine">
    <span class="line kicker c-teal">Studio Habits for</span>
    <span class="line title"><span class="c-white">LASTING</span> <span class="c-rose">ENERGY</span></span>
    <span class="line spaced spaced--small">Past Midlife - Zero Gym Needed</span>
  </div>
</section>

<!-- Row 3: split layouts -->
<section class="card col-1 row-3">
  <div class="photo" role="img" aria-label="Smiling woman in a white cropped sweater standing in a kitchen" style="left:0;top:0;width:129px;height:323px;background:linear-gradient(180deg,#7a5a48 0%,#d9ccc6 45%,#f1ece9 70%,#2d2a2b 100%)"></div>
  <span class="abs line c-rose" style="left:141px;top:44px;font-size:20px;font-weight:500">Ten-Week</span>
  <span class="abs line c-pine" style="left:140px;top:72px;font-size:34px;font-weight:700">BRIGHT</span>
  <span class="abs line c-pine" style="left:140px;top:114px;font-size:28px;font-weight:600">Morning</span>
  <div class="band band--pine" style="top:219px;height:67px;align-items:center;padding-left:0">
    <span class="line spaced" style="font-size:30px;letter-spacing:6px;color:var(--rose-text)">Reboot</span>
  </div>
</section>

<section class="card col-2 row-3">
  <div class="abs" style="left:0;top:0;width:48px;height:323px;background:var(--rose)"></div>
  <div class="abs" style="left:48px;top:-2px;width:250px;height:186px;background:var(--pine);border-radius:0 0 125px 125px / 0 0 110px 110px;box-shadow:0 0 0 3px var(--white)"></div>
  <div class="photo photo--round" role="img" aria-label="Dark wooden table ringed with vegetables, fruit, fish and a meal plan notebook" style="left:-3px;top:211px;width:230px;height:230px;border:3px solid var(--white);background:radial-gradient(circle at 50% 40%,#f4f2ee 0%,#5b3a2b 30%,#7d4a34 60%,#c2452f 100%)"></div>
  <div class="abs" style="left:56px;top:36px;width:196px;display:flex;flex-direction:column;align-items:center;gap:4px">
    <span class="line c-rose" style="font-size:36px;font-weight:600">Quick</span>
    <span class="line c-white" style="font-size:25px;font-weight:700">GARDEN KITCHEN</span>
    <span class="line spaced" style="font-size:16px;letter-spacing:4px">Menu Guide</span>
  </div>
</section>

<section class="card col-3 row-3">
  <div class="photo" role="img" aria-label="Two women in casual tops whispering against a blue backdrop" style="left:38px;top:0;width:183px;height:191px;border-radius:0 0 92px 92px;background:linear-gradient(180deg,#6fc9d8 0%,#7ccfdc 55%,#c9a58f 100%)"></div>
  <span class="abs line c-pine" style="left:0;width:259px;text-align:center;top:198px;font-size:24px;font-weight:600">Studio Habits for</span>
  <span class="abs line c-rose" style="left:0;width:259px;text-align:center;top:235px;font-size:33px;font-weight:700">LASTING ENERGY</span>
  <div class="band band--pine" style="top:286px;height:37px;align-items:center;padding-left:0">
    <span class="line" style="font-size:18px;font-weight:500">Past Midlife - Zero Gym Needed</span>
  </div>
</section>

</body>
</html>
```